Heron Loan Partners Business Card

We need a business card design for our mortgage servicing company. In addition to servicing the loans of homeowners, we help homeowners with purchasing their homes and any mortgage refinancing. We would like to see designs that use the colors in the logo attached below (gold-ish yellow and navy blue), and any other design you deem fit! The design should communicate a simpler life with smart mortgages provided by Heron.

```html
<!DOCTYPE html>
<html lang="en">
<head>
<meta charset="utf-8">
<title>Heron Loan Partners Business Card</title>
<link rel="stylesheet" href="https://fonts.googleapis.com/css2?family=Montserrat:wght@400;500;700;800&display=swap">
<style>
  :root {
    --navy: #201c55;
    --gold: #e1b23c;
    --paper: #ffffff;
    --ink: #1c1c1c;
    --backdrop: #2a2a2c;
  }
  * { box-sizing: border-box; margin: 0; padding: 0; }
  html, body {
    width: 1200px;
    height: 880px;
    overflow: hidden;
    background: var(--backdrop);
    font-family: "Montserrat", sans-serif;
  }
  .canvas {
    position: relative;
    width: 1200px;
    height: 880px;
  }
  .card {
    position: absolute;
    width: 560px;
    height: 320px;
    background: var(--paper);
    overflow: hidden;
    box-shadow: 0 12px 30px rgba(0,0,0,0.45);
  }
  .card--front { left: 150px; top: 80px; }
  .card--back  { left: 490px; top: 480px; }

  .brand {
    display: flex;
    align-items: center;
    gap: 10px;
    color: var(--gold);
    font-weight: 800;
    line-height: 1;
    white-space: nowrap;
  }
  .brand__mark {
    width: 14px;
    height: 14px;
    border-radius: 50%;
    background: var(--navy);
    flex: none;
  }
  .card--front .brand {
    position: absolute;
    left: 0; right: 0; top: 0; bottom: 0;
    justify-content: center;
    font-size: 40px;
    gap: 12px;
  }
  .card--front .brand__mark { width: 24px; height: 24px; }

  .card--back .brand {
    position: absolute;
    left: 34px;
    top: 150px;
    font-size: 19px;
  }

  .divider {
    position: absolute;
    left: 304px;
    top: 56px;
    width: 2px;
    height: 124px;
    background: var(--gold);
  }
  .contact {
    position: absolute;
    left: 322px;
    top: 44px;
    color: var(--ink);
  }
  .contact__name {
    font-weight: 800;
    font-size: 15px;
    letter-spacing: 0.02em;
    color: var(--navy);
  }
  .contact__name span { color: var(--gold); }
  .contact__role {
    font-size: 12px;
    margin-top: 3px;
    margin-bottom: 16px;
  }
  .contact__list { list-style: none; }
  .contact__item {
    display: flex;
    align-items: center;
    gap: 8px;
    font-size: 12px;
    margin-bottom: 7px;
  }
  .contact__item svg { width: 13px; height: 13px; flex: none; }

  .wave {
    position: absolute;
    left: 0; top: 0;
    width: 560px;
    height: 320px;
  }
</style>
</head>
<body>
<main class="canvas">
  <section class="card card--front" aria-label="Card front">
    <div class="brand"><span class="brand__mark"></span>Heron Loan Partners</div>
  </section>

  <section class="card card--back" aria-label="Card back">
    <svg class="wave" viewBox="0 0 560 320" aria-hidden="true">
      <path d="M0 308 C110 262 230 246 340 232 C440 219 515 205 560 178 L560 320 L0 320 Z" fill="var(--gold)"/>
      <path d="M0 308 C110 262 230 246 340 232 C440 219 515 205 560 178" fill="none" stroke="var(--navy)" stroke-width="4"/>
    </svg>

    <div class="brand"><span class="brand__mark"></span>Heron Loan Partners</div>

    <div class="divider"></div>

    <div class="contact">
      <p class="contact__name">DARA <span>WELLSBY</span></p>
      <p class="contact__role">Owner</p>
      <ul class="contact__list">
        <li class="contact__item">
          <svg viewBox="0 0 16 16" aria-hidden="true"><path fill="var(--gold)" d="M3 1h3l1.5 4-2 1.5a9 9 0 0 0 4 4L11 8.5l4 1.5v3a2 2 0 0 1-2 2A12 12 0 0 1 1 3a2 2 0 0 1 2-2z"/></svg>
          555.204.1187
        </li>
        <li class="contact__item">
          <svg viewBox="0 0 16 16" aria-hidden="true"><rect x="1" y="3" width="14" height="10" fill="var(--gold)"/><path d="M1 3l7 6 7-6" fill="none" stroke="#fff" stroke-width="1.4"/></svg>
          info@heronloanpartners.com
        </li>
        <li class="contact__item">
          <svg viewBox="0 0 16 16" aria-hidden="true"><circle cx="8" cy="8" r="7" fill="var(--gold)"/><path d="M1 8h14M8 1c-3 3-3 11 0 14M8 1c3 3 3 11 0 14" fill="none" stroke="#fff" stroke-width="1"/></svg>
          www.heronloanpartners.com
        </li>
      </ul>
    </div>
  </section>
</main>
</body>
</html>
```